Develop website for Cloud Security Startup

Looking for a logo that conveys the outsourced security and management of clients data, systems and development in Tellix, Bri and Pindle with an emphasis on security and compliance

Target Market(s)

Companies looking for professional services IT firm

Coding

Coded - Design and coding required

Number of Pages Required

5+ page

Font styles to use
Sans Serif

Colors
0455a3
33a6d7

Requirements
Must have
• Landing Page
- Help me get started

Move to the cloud safely
- Benefits of Cloud

What we do
- Cloud Adoption
- Managed Services
- Optimise

Resources
- News
- Resources
- Events
- Webinars
- Not for profit
- Case Studies
- Support Button
- Incident Button

Company
- About Us
- Why Vorplexa?
- Acreditations
- Quorvane Tellix Partner
- Net Promoter Score
- Careers
- Contact Us

Contact Us

```html
<!DOCTYPE html>
<html lang="en">
<head>
<meta charset="utf-8">
<title>Vorplexa – Cloud Security</title>
<link rel="stylesheet" href="https://fonts.googleapis.com/css2?family=Montserrat:wght@600;700;800&family=Raleway:wght@400;500;600&family=Lato:wght@400;700&display=swap">
<style>
:root{
  --brand-blue:#0455a3;
  --sky:#33a6d7;
  --bright:#1aa3e8;
  --navy:#0c2c8e;
  --deep:#071a5c;
  --ink:#111;
  --muted:#8a8f99;
  --body:#333;
  --white:#fff;
  --card-line:#eef0f4;
}
*{margin:0;padding:0;box-sizing:border-box}
html,body{width:1200px;height:3147px;overflow:hidden;background:var(--white)}
body{position:relative;font-family:'Raleway',sans-serif;color:var(--body)}
.abs{position:absolute}
a{color:inherit;text-decoration:none}

/* header */
.top-rule{left:0;top:0;width:1200px;height:9px;background:var(--deep)}
.top-rule span{position:absolute;left:437px;width:345px;height:100%;background:var(--bright)}
.site-header{left:0;top:9px;width:1200px;height:117px;background:var(--white)}
.brand{left:110px;top:26px;width:108px;display:flex;flex-direction:column;align-items:center;gap:6px;font-family:'Montserrat',sans-serif;font-weight:700;font-size:16px;line-height:18px;color:var(--brand-blue);letter-spacing:.5px}
.brand i{width:38px;height:38px;border-radius:50%;background:var(--brand-blue);display:block}
.main-nav{left:260px;top:53px;display:flex;gap:36px;font-family:'Lato',sans-serif;font-size:16px;color:#222;white-space:nowrap}
.main-nav a.active{color:var(--bright)}
.login{left:960px;top:40px;width:128px;height:44px;border-radius:3px;background:linear-gradient(180deg,#0b4fb0,#063a8c);color:#fff;font-family:'Lato',sans-serif;font-weight:700;font-size:16px;display:flex;align-items:center;justify-content:center;gap:12px}

/* hero */
.hero{left:0;top:126px;width:1200px;height:610px}
.hero-title{left:108px;top:228px;font-family:'Montserrat',sans-serif;font-weight:700;font-size:56px;line-height:68px;color:#fff}
.hero-sub{left:110px;top:302px;width:400px;font-family:'Montserrat',sans-serif;font-weight:600;font-size:17px;line-height:26px;color:#fff}
.btn{display:flex;align-items:center;justify-content:center;gap:10px;font-family:'Montserrat',sans-serif;font-weight:800;font-size:16px;color:#fff;background:var(--bright);border-radius:2px;white-space:nowrap}
.hero-btn{left:110px;top:386px;width:166px;height:48px}
.arrow-dot{width:40px;height:40px;border-radius:50%;background:var(--bright);display:flex;align-items:center;justify-content:center}

/* about */
.about-photo{left:121px;top:819px;width:357px;height:320px;background:linear-gradient(135deg,#0f3a4a,#16333f 45%,#1f6a78);box-shadow:0 4px 14px rgba(0,0,0,.2)}
.about-card{left:379px;top:1004px;width:170px;height:168px;background:#dde8f1;box-shadow:0 4px 14px rgba(0,0,0,.15);display:flex;align-items:center;justify-content:center;gap:8px;font-family:'Raleway',sans-serif;font-weight:600;font-size:20px;color:var(--brand-blue)}
.about-card i{width:18px;height:18px;border-radius:50%;background:var(--brand-blue);display:block}
.section-title{font-family:'Montserrat',sans-serif;font-weight:700;font-size:36px;line-height:44px;color:var(--ink);white-space:nowrap}
.about-title{left:623px;top:828px}
.rule{height:4px;width:55px;background:var(--bright)}
.about-rule{left:623px;top:879px}
.about-text{left:623px;top:910px;width:462px;font-size:16.5px;line-height:28.3px;color:#222}
.about-btn{left:623px;top:1106px;width:165px;height:48px}

/* benefits */
.benefits{left:0;top:1262px;width:604px;height:524px;background:linear-gradient(135deg,#2eaee6,#239fd8 60%,#1b8cc8)}
.benefits-photo{left:604px;top:1262px;width:596px;height:524px;background:radial-gradient(circle at 45% 45%,#dfeaf3 0,#aec6da 35%,#2a3344 75%,#1a1f28)}
.benefits-title{left:78px;top:1306px;color:#fff}
.benefits-rule{left:80px;top:1355px;background:#fff}
.benefit-list{left:80px;top:1398px;list-style:none;color:#fff;font-size:16.5px;font-weight:500}
.benefit-list li{height:56.5px;display:flex;align-items:flex-start;gap:28px;white-space:nowrap}
.benefit-list svg{margin-top:4px}
.outline-btn{left:81px;top:1686px;width:165px;height:47px;border:1.5px solid #fff;background:transparent}

/* what we do */
.wwd-title{left:0;top:1866px;width:1200px;text-align:center}
.wwd-rule{left:572px;top:1914px}
.service{top:2032px;width:304px;height:244px;background:#fff;border:1px solid var(--card-line);text-align:center}
.service.featured{background:var(--navy);border-color:var(--navy)}
.service h3{margin-top:80px;font-family:'Montserrat',sans-serif;font-weight:700;font-size:15px;color:var(--ink)}
.service p{margin:12px auto 0;width:262px;font-size:15.5px;line-height:24px;color:var(--muted)}
.service.featured h3,.service.featured p{color:#fff}
.service-icon{top:1973px;width:100px;height:100px;border-radius:50%;background:var(--bright);display:flex;align-items:center;justify-content:center}
.service-icon.featured{background:var(--navy);border:3px solid #fff}
.go{width:27px;height:27px;border-radius:50%;background:var(--bright);display:flex;align-items:center;justify-content:center;top:2263px}
.go.dark{background:#fff;border:1.5px solid var(--navy)}

/* news */
.news{left:0;top:2364px;width:1200px;height:420px;background:linear-gradient(180deg,#0d2f95,#0a2886)}
.news-title{left:0;top:2407px;width:1200px;text-align:center;color:#fff}
.news-rule{left:572px;top:2461px}
.news-card{top:2526px;width:450px;height:184px;background:#fff}
.news-photo{position:absolute;left:6px;top:5px;width:151px;height:173px;background:linear-gradient(135deg,#c9d3dc,#8d99a6 55%,#4c5560)}
.news-photo.alt{background:linear-gradient(135deg,#e2edf6,#a9c3da 55%,#5b6f84)}
.badge{position:absolute;left:10px;top:11px;width:48px;height:44px;background:var(--bright);color:#fff;text-align:center;font-family:'Montserrat',sans-serif;font-weight:800;font-size:18px;line-height:20px;padding-top:3px}
.badge small{display:block;font-size:11px;font-weight:700;line-height:14px}
.news-body{position:absolute;left:172px;top:18px;width:268px}
.news-body h4{font-family:'Montserrat',sans-serif;font-weight:700;font-size:13.5px;color:var(--ink);white-space:nowrap}
.news-date{margin-top:8px;font-size:10.5px;color:var(--bright);display:flex;align-items:center;gap:8px}
.news-body p{margin-top:8px;font-size:15px;line-height:22px;color:var(--muted)}
.read{margin-top:10px;font-size:14.5px;font-weight:600;color:var(--bright);display:flex;align-items:center;gap:12px}

/* footer */
.footer-bg{left:0;top:2760px;width:1200px;height:387px}
.footer-brand{left:0;top:2872px;width:1200px;display:flex;flex-direction:column;align-items:center;gap:6px;font-family:'Montserrat',sans-serif;font-weight:700;font-size:18px;line-height:20px;color:var(--bright)}
.footer-brand i{width:32px;height:32px;border-radius:50%;background:var(--bright);display:block}
.footer-nav{left:0;top:2976px;width:1200px;display:flex;justify-content:center;gap:24px;font-family:'Lato',sans-serif;font-size:15.5px;color:#fff}
.footer-contact{left:0;top:3025px;width:1200px;display:flex;justify-content:center;gap:56px;font-family:'Lato',sans-serif;font-size:15.5px;color:#fff}
.footer-contact span{display:flex;align-items:center;gap:6px}
.footer-rule{left:111px;top:3083px;width:977px;height:1px;background:#555}
.socials{left:111px;top:3112px;display:flex;gap:16px}
.socials i{width:12px;height:12px;border-radius:50%;border:1.5px solid #fff;display:block}
.copyright{left:0;top:3108px;width:1200px;text-align:center;font-family:'Lato',sans-serif;font-size:15px;color:#fff;white-space:pre}
</style>
</head>
<body>

<div class="abs top-rule"><span></span></div>
<header class="abs site-header"></header>
<div class="abs brand"><i></i>VORPLEXA</div>
<nav class="abs main-nav">
  <a class="active">HOME</a>
  <a>BENEFITS</a>
  <a>WHAT WE DO</a>
  <a>RESOURCES</a>
  <a>COMPANY</a>
  <a>CONTACT US</a>
</nav>
<a class="abs login">Login
  <svg width="14" height="14" viewBox="0 0 14 14"><path d="M1 7h8M6 4l3 3-3 3M10 2h3v10h-3" stroke="#fff" stroke-width="2" fill="none"/></svg></a>

<!-- hero -->
<svg class="abs hero" viewBox="0 126 1200 610" width="1200" height="610">
  <defs>
    <linearGradient id="heroFill" x1="0" y1="0" x2="1" y2="0.6">
      <stop offset="0" stop-color="#0fd0e0"/>
      <stop offset=".35" stop-color="#0a6fae"/>
      <stop offset="1" stop-color="#0a1f6e"/>
    </linearGradient>
    <radialGradient id="artFill" cx=".6" cy=".45" r=".6">
      <stop offset="0" stop-color="#2b6fe0"/>
      <stop offset=".5" stop-color="#123c9a"/>
      <stop offset="1" stop-color="#0b2a78" stop-opacity="0"/>
    </radialGradient>
  </defs>
  <path d="M0 126H1200V556C1050 610 900 700 770 727C700 740 640 720 560 690C380 630 180 600 0 574Z" fill="url(#heroFill)"/>
  <rect role="img" aria-label="Illustration of a laptop linked to a data cloud with glowing security interfaces" x="400" y="130" width="790" height="480" fill="url(#artFill)"/>
  <path d="M730 733C900 715 1050 620 1200 556V566C1050 630 900 728 760 733Z" fill="#1aa3e8"/>
</svg>
<h1 class="abs hero-title">Vorplexa</h1>
<p class="abs hero-sub">Lorem ipsum dolor sit  consectetur adipiscing elit sed do eiusmod tempor incididunt</p>
<a class="abs btn hero-btn">GET STARETED
  <svg width="14" height="14" viewBox="0 0 14 14"><circle cx="7" cy="7" r="6.5" fill="#fff"/><path d="M6 4l3 3-3 3" stroke="#1aa3e8" stroke-width="2" fill="none"/></svg></a>
<div class="abs arrow-dot" style="left:37px;top:337px"><svg width="12" height="14" viewBox="0 0 12 14"><path d="M8 2L3 7l5 5" stroke="#fff" stroke-width="3" fill="none"/></svg></div>
<div class="abs arrow-dot" style="left:1122px;top:298px"><svg width="12" height="14" viewBox="0 0 12 14"><path d="M4 2l5 5-5 5" stroke="#fff" stroke-width="3" fill="none"/></svg></div>

<!-- about -->
<div class="abs about-photo" role="img" aria-label="Photo of an engineer holding a laptop in a server room"></div>
<div class="abs about-card"><i></i>Vorplexa</div>
<h2 class="abs section-title about-title">ABOUT  VORPLEXA</h2>
<div class="abs rule about-rule"></div>
<p class="abs about-text">Lorem ipsum dolor sit amet, consectetur adipiscing elit, sed do eiusmod tempor incididunt ut labore et dolore magna aliqua. Ut enim ad minim veniam, quis nostrud exercitation ullamco laboris nisi ut aliquip ex ea commodo consequat. Duis aute irure dolor in reprehenderit in voluptate velit esse cillum dolore eu fugiat nulla admit pariatur,</p>
<a class="abs btn about-btn">LEARN MORE
  <svg width="14" height="14" viewBox="0 0 14 14"><circle cx="7" cy="7" r="6.5" fill="#fff"/><path d="M6 4l3 3-3 3" stroke="#1aa3e8" stroke-width="2" fill="none"/></svg></a>

<!-- benefits -->
<div class="abs benefits"></div>
<div class="abs benefits-photo" role="img" aria-label="Photo of a hand holding a glowing padlock shield"></div>
<h2 class="abs section-title benefits-title">BENEFITS</h2>
<div class="abs rule benefits-rule"></div>
<ul class="abs benefit-list">
  <li><svg width="16" height="14" viewBox="0 0 16 14"><path d="M2 7l4 4 8-9" stroke="#fff" stroke-width="3" fill="none"/></svg>Lorem ipsum dolor sit amet, consectetur adipiscing</li>
  <li><svg width="16" height="14" viewBox="0 0 16 14"><path d="M2 7l4 4 8-9" stroke="#fff" stroke-width="3" fill="none"/></svg>Lorem ipsum dolor sit amet, consectetur adipiscing</li>
  <li><svg width="16" height="14" viewBox="0 0 16 14"><path d="M2 7l4 4 8-9" stroke="#fff" stroke-width="3" fill="none"/></svg>Lorem ipsum dolor sit amet, consectetur adipiscing</li>
  <li><svg width="16" height="14" viewBox="0 0 16 14"><path d="M2 7l4 4 8-9" stroke="#fff" stroke-width="3" fill="none"/></svg>Lorem ipsum dolor sit amet, consectetur adipiscing</li>
  <li><svg width="16" height="14" viewBox="0 0 16 14"><path d="M2 7l4 4 8-9" stroke="#fff" stroke-width="3" fill="none"/></svg>Lorem ipsum dolor sit amet, consectetur adipiscing</li>
</ul>
<a class="abs btn outline-btn">LEARN MORE
  <svg width="14" height="14" viewBox="0 0 14 14"><circle cx="7" cy="7" r="6.5" fill="#fff"/><path d="M6 4l3 3-3 3" stroke="#2aa6df" stroke-width="2" fill="none"/></svg></a>

<!-- what we do -->
<h2 class="abs section-title wwd-title">WHAT WE DO</h2>
<div class="abs rule wwd-rule"></div>

<div class="abs service" style="left:110px"><h3>CLOUD ADOPTION</h3><p>Lorem ipsum dolor consectetur adipiscing elit, sed do eiusmod tempor incididuefnt dolore magna aliqua enimveniam.</p></div>
<div class="abs service featured" style="left:447px"><h3>MANAGED SERVICES</h3><p>Lorem ipsum dolor consectetur adipiscing elit, sed do eiusmod tempor incididuefnt dolore magna aliqua enimveniam.</p></div>
<div class="abs service" style="left:784px"><h3>OPTIMISE</h3><p>Lorem ipsum dolor consectetur adipiscing elit, sed do eiusmod tempor incididuefnt dolore magna aliqua enimveniam.</p></div>

<div class="abs service-icon" style="left:211px"><svg width="50" height="40" viewBox="0 0 50 40"><path d="M12 30a8 8 0 0 1 1-16 12 12 0 0 1 23 2 7 7 0 0 1 2 14Z" stroke="#fff" stroke-width="2.5" fill="none"/><circle cx="20" cy="24" r="2" fill="#fff"/><circle cx="26" cy="24" r="2" fill="#fff"/><circle cx="32" cy="24" r="2" fill="#fff"/></svg></div>
<div class="abs service-icon featured" style="left:549px"><svg width="46" height="46" viewBox="0 0 46 46"><circle cx="23" cy="23" r="8" stroke="#fff" stroke-width="2.5" fill="none"/><path d="M23 6v6M23 34v6M6 23h6M34 23h6M11 11l4 4M31 31l4 4M35 11l-4 4M11 35l4-4" stroke="#fff" stroke-width="2.5"/></svg></div>
<div class="abs service-icon" style="left:886px"><svg width="46" height="40" viewBox="0 0 46 40"><rect x="4" y="4" width="30" height="24" stroke="#fff" stroke-width="2.5" fill="none"/><path d="M4 10h30M10 16h14M10 21h10" stroke="#fff" stroke-width="2"/><circle cx="36" cy="30" r="6" stroke="#fff" stroke-width="2.5" fill="none"/></svg></div>

<div class="abs go" style="left:248px"><svg width="8" height="10" viewBox="0 0 8 10"><path d="M2 1l4 4-4 4" stroke="#fff" stroke-width="2" fill="none"/></svg></div>
<div class="abs go dark" style="left:586px"><svg width="8" height="10" viewBox="0 0 8 10"><path d="M2 1l4 4-4 4" stroke="#0c2c8e" stroke-width="2" fill="none"/></svg></div>
<div class="abs go" style="left:923px"><svg width="8" height="10" viewBox="0 0 8 10"><path d="M2 1l4 4-4 4" stroke="#fff" stroke-width="2" fill="none"/></svg></div>

<!-- news -->
<section class="abs news"></section>
<h2 class="abs section-title news-title">OUR NEWS</h2>
<div class="abs rule news-rule"></div>

<article class="abs news-card" style="left:130px">
  <div class="news-photo" role="img" aria-label="Photo of hands typing on a laptop with security overlay"></div>
  <div class="badge">25<small>May</small></div>
  <div class="news-body">
    <h4>LOREM  CONSECTETUR ADIPISCING</h4>
    <div class="news-date"><svg width="9" height="9" viewBox="0 0 9 9"><rect x="0.5" y="1.5" width="8" height="7" fill="#1aa3e8"/></svg>25.4.2021</div>
    <p>Lorem ipsum dolor  consectetur adipiscing elit, sed do eiusmod tempor incididunt dolore magna</p>
    <div class="read">Read More <svg width="14" height="14" viewBox="0 0 14 14"><circle cx="7" cy="7" r="6.5" fill="#1aa3e8"/><path d="M6 4l3 3-3 3" stroke="#fff" stroke-width="2" fill="none"/></svg></div>
  </div>
</article>
<article class="abs news-card" style="left:620px">
  <div class="news-photo alt" role="img" aria-label="Photo of a keyboard with a cloud padlock overlay"></div>
  <div class="badge">25<small>May</small></div>
  <div class="news-body">
    <h4>LOREM  CONSECTETUR ADIPISCING</h4>
    <div class="news-date"><svg width="9" height="9" viewBox="0 0 9 9"><rect x="0.5" y="1.5" width="8" height="7" fill="#1aa3e8"/></svg>25.4.2021</div>
    <p>Lorem ipsum dolor  consectetur adipiscing elit, sed do eiusmod tempor incididunt dolore magna</p>
    <div class="read">Read More <svg width="14" height="14" viewBox="0 0 14 14"><circle cx="7" cy="7" r="6.5" fill="#1aa3e8"/><path d="M6 4l3 3-3 3" stroke="#fff" stroke-width="2" fill="none"/></svg></div>
  </div>
</article>

<!-- footer -->
<svg class="abs footer-bg" viewBox="0 2760 1200 387" width="1200" height="387">
  <rect x="0" y="2760" width="1200" height="387" fill="#0a2886"/>
  <path d="M0 2981C150 2910 320 2830 430 2812C520 2800 800 2880 1200 2957V3147H0Z" fill="#1aa3e8"/>
  <path d="M0 2992C150 2920 320 2840 430 2824C520 2812 800 2892 1200 2970V3147H0Z" fill="#000"/>
</svg>
<div class="abs footer-brand"><i></i>VORPLEXA</div>
<nav class="abs footer-nav"><a>Home</a><a>Benefits</a><a>What we do</a><a>Resources</a><a>Company</a><a>Contact Us</a></nav>
<div class="abs footer-contact">
  <span><svg width="13" height="13" viewBox="0 0 13 13"><path d="M2 1l3 3-1.5 1.5a8 8 0 0 0 4 4L9 8l3 3-2 2C5 12 1 8 0 3Z" fill="#1aa3e8"/></svg>555 (014) 782</span>
  <span><svg width="11" height="15" viewBox="0 0 11 15"><path d="M5.5 0A5.5 5.5 0 0 0 0 5.5C0 9 5.5 15 5.5 15S11 9 11 5.5A5.5 5.5 0 0 0 5.5 0Z" fill="#1aa3e8"/></svg>Lorem ipsum dolor sit amet,</span>
  <span><svg width="15" height="11" viewBox="0 0 15 11"><rect x="1" y="1" width="13" height="9" stroke="#1aa3e8" stroke-width="1.5" fill="none"/><path d="M1 1l6.5 5L14 1" stroke="#1aa3e8" stroke-width="1.5" fill="none"/></svg>info@vorplexa.com</span>
</div>
<div class="abs footer-rule"></div>
<div class="abs socials"><i></i><i></i><i></i><i></i></div>
<p class="abs copyright">©Copyrights 2021 Vorplexa.   |    All Rights Reserved   |</p>

</body>
</html>
```